Carpet cleaning company focused on high quality needs business cards

We are a growing company that just merged with another company and need to design a new business card. We do both residential as well as commercial cleaning. We do carpet, tile & grout, upholstery, hard floors, and stain & pet odor removal. We treat our customers like family and strive to achieve outstanding results with every job.

```html
<!DOCTYPE html>
<html lang="en">
<head>
<meta charset="UTF-8">
<title>Bright Path Steam Cleaning – Business Cards</title>
<link rel="stylesheet" href="https://fonts.googleapis.com/css2?family=Poppins:wght@400;500;700&family=Oswald:wght@500&display=swap">
<style>
  :root {
    --bg: #2c2c2c;
    --card-white: #ffffff;
    --brand-red: #ef4640;
    --ink: #1d1d1d;
    --art-red: #e8413b;
    --art-blue: #2b78c2;
    --art-tan: #c9a66b;
  }
  * { margin: 0; padding: 0; box-sizing: border-box; }
  html, body { width: 1200px; height: 689px; overflow: hidden; }
  body {
    background: var(--bg);
    font-family: "Poppins", Arial, sans-serif;
    position: relative;
  }
  .card {
    position: absolute;
    top: 190px;
    width: 540px;
    height: 310px;
    border-radius: 18px;
    background: var(--card-white);
    overflow: hidden;
  }
  .card--front { left: 30px; }
  .card--back { left: 630px; }

  /* Front */
  .front__band {
    position: absolute; left: 0; right: 0; bottom: 0; height: 118px;
    background: var(--brand-red);
  }
  .mascot-art {
    position: absolute;
    border-radius: 2px;
    background: linear-gradient(160deg, var(--art-blue) 0%, var(--art-blue) 30%, var(--art-red) 55%, var(--art-red) 100%);
  }
  .front__art { left: 110px; top: 36px; width: 140px; height: 148px; }
  .front__brand {
    position: absolute; left: 272px; top: 58px;
    color: var(--ink); font-weight: 700; line-height: 0.98;
  }
  .front__brand-main { font-size: 46px; letter-spacing: -1px; display: block; }
  .front__brand-sub { font-size: 24px; display: block; margin-top: 4px; letter-spacing: 0.5px; }
  .front__services {
    position: absolute; left: 0; right: 0; top: 212px;
    text-align: center; color: #fff; font-size: 15px; line-height: 1.45; font-weight: 400;
  }

  /* Back */
  .back__band-bottom {
    position: absolute; left: 0; right: 0; bottom: 0; height: 112px;
    background: var(--brand-red);
  }
  .back__band-side {
    position: absolute; left: 330px; right: 0; top: 60px; bottom: 0;
    background: var(--brand-red);
  }
  .back__frame {
    position: absolute; left: 345px; top: 24px; width: 160px; height: 168px;
    background: var(--card-white); padding: 8px;
  }
  .back__frame .mascot-art { position: static; width: 100%; height: 100%; }
  .back__person { position: absolute; left: 36px; top: 58px; }
  .back__name { color: var(--brand-red); font-weight: 700; font-size: 25px; line-height: 1.1; }
  .back__role { color: var(--ink); font-size: 14px; }
  .back__address { color: var(--ink); font-size: 14px; line-height: 1.35; margin-top: 20px; }
  .back__contacts {
    position: absolute; left: 36px; top: 214px;
    list-style: none; color: #fff; font-size: 14px; line-height: 1.6;
  }
  .back__contacts li { display: flex; align-items: center; gap: 10px; }
  .back__contacts svg { width: 14px; height: 14px; flex: none; }
  .back__tagline {
    position: absolute; right: 24px; top: 212px;
    font-family: "Oswald", "Arial Narrow", sans-serif; font-weight: 500;
    color: #fff; font-size: 16px; letter-spacing: 0.3px;
  }
</style>
</head>
<body>

<section class="card card--front">
  <div class="front__band"></div>
  <div class="mascot-art front__art" role="img" aria-label="Cartoon cleaning technician holding a steam wand in front of a red burst"></div>
  <div class="front__brand">
    <span class="front__brand-main">Bright Path</span>
    <span class="front__brand-sub">STEAM CLEANING</span>
  </div>
  <p class="front__services">
    Carpet • Tile &amp; Grout • Upholstery<br>
    Hard floors &amp; Stain • Pet Odor Removal
  </p>
</section>

<section class="card card--back">
  <div class="back__band-bottom"></div>
  <div class="back__band-side"></div>
  <div class="back__frame">
    <div class="mascot-art" role="img" aria-label="Cartoon cleaning technician holding a steam wand in front of a red burst"></div>
  </div>
  <div class="back__person">
    <p class="back__name">Daniel Hart</p>
    <p class="back__role">Managing Director</p>
    <p class="back__address">421, Address line here<br>Country Name, 45452</p>
  </div>
  <ul class="back__contacts">
    <li>
      <svg viewBox="0 0 24 24" fill="#fff" aria-hidden="true"><path d="M6.6 10.8a15.1 15.1 0 0 0 6.6 6.6l2.2-2.2a1 1 0 0 1 1-.25 11.4 11.4 0 0 0 3.6.57 1 1 0 0 1 1 1V20a1 1 0 0 1-1 1A17 17 0 0 1 3 4a1 1 0 0 1 1-1h3.5a1 1 0 0 1 1 1c0 1.25.2 2.45.57 3.57a1 1 0 0 1-.25 1z"/></svg>
      555-010 2468
    </li>
    <li>
      <svg viewBox="0 0 24 24" fill="#fff" aria-hidden="true"><path d="M2 5h20v14H2z M3.5 6.5 12 13l8.5-6.5" stroke="#ef4640" stroke-width="1.5"/></svg>
      info@brightpathsteam.com
    </li>
    <li>
      <svg viewBox="0 0 24 24" fill="none" stroke="#fff" stroke-width="2" aria-hidden="true"><circle cx="12" cy="12" r="9"/><path d="M3 12h18M12 3c3 3 3 15 0 18M12 3c-3 3-3 15 0 18"/></svg>
      www.brightpathsteam.com
    </li>
  </ul>
  <p class="back__tagline">RESIDENTIAL &amp; COMMERCIAL CLEANING</p>
</section>

</body>
</html>
```